BildeVOLD buisnesscard

Hey :) I need a modern buisnesscard for my company BildeVOLD
It most have:
Dagligleder og Fotograf: Henrik Audun Strandvik

Mob: +4791264085
Epost: post@bildevold.example
Adresse: Kvernbakken9, 6040 Sjøholmen

Facbook and instagram logo with text BildeVOLD

BildeVOLD logo

It Company

```html
<!DOCTYPE html>
<html lang="en">
<head>
<meta charset="utf-8">
<title>BildeVOLD business card</title>
<link rel="stylesheet" href="https://fonts.googleapis.com/css2?family=Exo+2:wght@600&family=Roboto:wght@400&display=swap">
<style>
  :root {
    --page-bg: #e4e4e4;
    --front-top: #bdbec0;
    --front-bottom: #8c8e91;
    --back-bg: #f7f7f7;
    --ink: #8f9194;
    --ink-soft: #9a9c9f;
    --band: #8e9093;
    --rule: #a7a9ab;
    --white: #ffffff;
  }
  * { margin: 0; padding: 0; box-sizing: border-box; }
  html, body { width: 1200px; height: 576px; overflow: hidden; }
  body { background: var(--page-bg); position: relative; font-family: "Roboto", Arial, sans-serif; }

  .card {
    position: absolute;
    top: 138px;
    border-radius: 6px;
    overflow: hidden;
  }

  /* Front side */
  .card-front {
    left: 82px;
    width: 485px;
    height: 295px;
    background: radial-gradient(ellipse at 50% 10%, var(--front-top) 0%, var(--front-bottom) 100%);
  }
  .front-brand {
    position: absolute;
    left: 0; right: 0;
    top: 126px;
    text-align: center;
    font-family: "Exo 2", Arial, sans-serif;
    font-weight: 600;
    font-size: 40px;
    line-height: 1;
    color: var(--white);
    letter-spacing: 0.5px;
  }

  /* Back side */
  .card-back {
    left: 602px;
    width: 481px;
    height: 292px;
    background: var(--back-bg);
  }
  .back-band {
    position: absolute;
    left: 0; right: 0; bottom: 0;
    height: 13px;
    background: var(--band);
  }
  .brand-square {
    position: absolute;
    left: 20px;
    top: 43px;
    width: 45px;
    height: 45px;
    background: var(--ink);
  }
  .brand-name {
    position: absolute;
    left: 104px;
    top: 44px;
    font-family: "Exo 2", Arial, sans-serif;
    font-weight: 600;
    font-size: 40px;
    line-height: 44px;
    color: var(--ink);
  }

  .holder { position: absolute; left: 20px; top: 163px; }
  .holder-name {
    font-family: "Exo 2", Arial, sans-serif;
    font-weight: 600;
    font-size: 17px;
    line-height: 22px;
    color: var(--ink);
  }
  .holder-title { font-size: 12px; line-height: 16px; color: var(--ink-soft); margin-top: 3px; }
  .website { position: absolute; left: 20px; top: 236px; font-size: 11.5px; color: var(--ink-soft); }

  .social {
    position: absolute; left: 242px; top: 164px;
    display: flex; align-items: center; gap: 6px;
    font-size: 13px; line-height: 18px; color: var(--ink-soft);
  }
  .social-square { width: 11px; height: 11px; background: var(--ink); border-radius: 2px; }
  .contact-rule {
    position: absolute; left: 242px; right: 0; top: 191px;
    height: 1.5px; background: var(--rule);
  }
  .contact-list { position: absolute; left: 242px; top: 201px; list-style: none; }
  .contact-list li {
    display: flex; align-items: center;
    height: 17.5px; font-size: 13px; color: var(--ink-soft);
  }
  .contact-list svg { width: 11px; height: 11px; margin-right: 12px; fill: var(--ink); }
</style>
</head>
<body>
  <section class="card card-front">
    <span class="front-brand">BildeVOLD</span>
  </section>

  <section class="card card-back">
    <span class="brand-square"></span>
    <span class="brand-name">BildeVOLD</span>

    <div class="holder">
      <p class="holder-name">Henrik Audun Strandvik</p>
      <p class="holder-title">Managing Director &amp; Photographer</p>
    </div>
    <p class="website">www.bildevold.example</p>

    <div class="social"><span class="social-square"></span>/BildeVOLD</div>
    <div class="contact-rule"></div>

    <ul class="contact-list">
      <li>
        <svg viewBox="0 0 12 12" aria-hidden="true"><path d="M3 0h6a1 1 0 0 1 1 1v10a1 1 0 0 1-1 1H3a1 1 0 0 1-1-1V1a1 1 0 0 1 1-1zm0.5 1.5v8h5v-8z"/></svg>
        +4791264085
      </li>
      <li>
        <svg viewBox="0 0 12 12" aria-hidden="true"><path d="M0 2h12v8H0zm1 1v0.4l5 3.3 5-3.3V3zm0 1.6V9h10V4.6L6 7.9z"/></svg>
        post@bildevold.example
      </li>
      <li>
        <svg viewBox="0 0 12 12" aria-hidden="true"><path d="M6 0a4 4 0 0 1 4 4c0 3-4 8-4 8S2 7 2 4a4 4 0 0 1 4-4zm0 2.3a1.7 1.7 0 1 0 0 3.4 1.7 1.7 0 0 0 0-3.4z"/></svg>
        Kvernbakken9, 6040 Sjøholmen
      </li>
    </ul>

    <div class="back-band"></div>
  </section>
</body>
</html>
```